Acupuncture business needs business card design

I need a business card for an acupuncture clinic called "Harbourlight Wellness"
It will need the following details:
My name: Marcus Pelling
Acupuncturist
Member TVBH
KWF Treatment Provider
Ph numbers: 581 2734 027 418 5620
Email: marcus@hbwel.example.nz
On the back it will need a table with 2 columns for appointments, one column for time and one for date.

Industry/Entity Type

Clinic

Contact Information for Business Card

Marcus Pelling
Acupuncturist
Member TVBH
KWF Treatment Provider
Email: marcus@hbwel.example.nz

Requirements
Must have
• Marcus Pelling
• Acupuncturist
• Member TVBH
• KWF Treatment Provider
• Ph numbers: 581 2734 027 418 5620
• Email: marcus@hbwel.example.nz
• On the back it will need a table with 2 columns for appointments, one column for time and one for date.

```html
<!DOCTYPE html>
<html lang="en">
<head>
<meta charset="utf-8">
<title>Harbourlight Wellness – Business Card</title>
<link rel="stylesheet" href="https://fonts.googleapis.com/css2?family=Exo+2:wght@400;500;600&display=swap">
<style>
  :root {
    --teal: #2b7f98;
    --cyan: #2aa7d6;
    --ink: #3a3f44;
    --muted: #6d7479;
    --rule: #cfe3ea;
    --card: #ffffff;
    --stage: #e9ecee;
  }
  * { box-sizing: border-box; margin: 0; padding: 0; }
  html, body { width: 1200px; height: 900px; overflow: hidden; }
  body {
    background: var(--stage);
    font-family: "Exo 2", sans-serif;
    display: flex;
    flex-direction: column;
    align-items: center;
    justify-content: center;
    gap: 40px;
  }
  .card {
    position: relative;
    width: 700px;
    height: 400px;
    background: var(--card);
    border-radius: 28px;
    overflow: hidden;
    box-shadow: 0 6px 18px rgba(0,0,0,.12);
  }
  .card__band { position: absolute; inset: 0; width: 100%; height: 100%; }

  /* Front */
  .identity { position: absolute; right: 40px; top: 38px; text-align: right; color: #fff; }
  .identity__name { font-size: 24px; font-weight: 500; letter-spacing: 1px; text-transform: uppercase; }
  .identity__role { font-size: 18px; margin-top: 6px; }

  .brand { position: absolute; left: 36px; top: 132px; display: flex; align-items: center; gap: 12px; }
  .brand__dot { width: 36px; height: 36px; border-radius: 50%; background: var(--cyan); flex: none; }
  .brand__name { font-size: 34px; font-weight: 500; color: var(--cyan); line-height: 1; }
  .brand__tagline { font-size: 12px; letter-spacing: 3.4px; color: var(--cyan); text-transform: uppercase; margin-top: 5px; }

  .contacts { position: absolute; left: 40px; top: 214px; list-style: none; }
  .contacts li { display: flex; align-items: center; gap: 12px; font-size: 15px; color: var(--muted); height: 28px; }
  .contacts svg { width: 16px; height: 16px; fill: var(--teal); flex: none; }

  .credentials { position: absolute; right: 44px; top: 222px; text-align: right; font-size: 16px; line-height: 1.6; color: var(--teal); font-weight: 500; }

  .address { position: absolute; right: 44px; bottom: 36px; text-align: right; font-size: 19px; line-height: 1.4; color: var(--ink); }

  /* Back */
  .back { display: flex; flex-direction: column; align-items: center; padding: 34px 60px; gap: 20px; }
  .back .brand { position: static; }
  .back .brand__dot { width: 44px; height: 44px; background: var(--teal); }
  .back .brand__name { font-size: 30px; }
  .back .brand__tagline { font-size: 11px; letter-spacing: 3.6px; }

  .appointments { width: 100%; border-collapse: collapse; font-size: 16px; color: var(--ink); }
  .appointments th {
    background: var(--teal); color: #fff; font-weight: 500; text-transform: uppercase;
    letter-spacing: 2px; font-size: 15px; height: 38px; text-align: center;
  }
  .appointments th:first-child { border-radius: 10px 0 0 0; }
  .appointments th:last-child { border-radius: 0 10px 0 0; }
  .appointments td { height: 44px; border-bottom: 1px solid var(--rule); }
  .appointments td:first-child { border-right: 1px solid var(--rule); }
</style>
</head>
<body>

<section class="card front" aria-label="Business card front">
  <svg class="card__band" viewBox="0 0 700 400" preserveAspectRatio="none" aria-hidden="true">
    <path d="M0 0 H700 V175 C520 92 260 62 0 82 Z" fill="var(--teal)"/>
    <path d="M0 94 C260 74 520 104 700 188" fill="none" stroke="var(--cyan)" stroke-width="5"/>
  </svg>

  <div class="identity">
    <p class="identity__name">Marcus Pelling</p>
    <p class="identity__role">Acupuncturist</p>
  </div>

  <div class="brand">
    <span class="brand__dot"></span>
    <div>
      <p class="brand__name">Harbourlight Wellness</p>
      <p class="brand__tagline">Acupuncture Physiotherapy</p>
    </div>
  </div>

  <ul class="contacts">
    <li><svg viewBox="0 0 16 16"><path d="M3 1h3l1.5 4-2 1.2a9 9 0 0 0 4.3 4.3L11 8.5l4 1.5v3a2 2 0 0 1-2 2A12 12 0 0 1 1 3a2 2 0 0 1 2-2z"/></svg>581 2734</li>
    <li><svg viewBox="0 0 16 16"><path d="M4 0h8a1 1 0 0 1 1 1v14a1 1 0 0 1-1 1H4a1 1 0 0 1-1-1V1a1 1 0 0 1 1-1zm1 2v10h6V2zm3 11a1 1 0 1 0 0 2 1 1 0 0 0 0-2z"/></svg>027 418 5620</li>
    <li><svg viewBox="0 0 16 16"><path d="M1 3h14v10H1zm1.5 1.5v.3L8 9l5.5-4.2v-.3z"/></svg>marcus@hbwel.example.nz</li>
    <li><svg viewBox="0 0 16 16"><path d="M8 0a8 8 0 1 0 0 16A8 8 0 0 0 8 0zm0 2a6 6 0 0 1 5.7 4H10.5A9 9 0 0 0 8 2zm-2 .3A9 9 0 0 0 5.5 6H2.3A6 6 0 0 1 6 2.3zM2 8h3.4v0a10 10 0 0 0 .1 2H2.3A6 6 0 0 1 2 8zm5 0h2v2H7zm3.6 2a10 10 0 0 0 0-2H14a6 6 0 0 1-.3 2zM5.5 12a9 9 0 0 0 .5 1.7A6 6 0 0 1 3.4 12zm2.5 2a7 7 0 0 1-1-2h2a7 7 0 0 1-1 2zm2 .7a9 9 0 0 0 .5-2.7h2.1a6 6 0 0 1-2.6 2.7z"/></svg>www.hbwel.example.nz</li>
  </ul>

  <div class="credentials">
    <p>Member TVBH</p>
    <p>KWF Treatment Provider</p>
  </div>

  <p class="address">112 4th floor Quay<br>Harbour Road TRG</p>
</section>

<section class="card back" aria-label="Business card back">
  <div class="brand">
    <span class="brand__dot"></span>
    <div>
      <p class="brand__name">Harbourlight Wellness</p>
      <p class="brand__tagline">Acupuncture Physiotherapy</p>
    </div>
  </div>

  <table class="appointments">
    <thead>
      <tr><th scope="col">Date</th><th scope="col">Time</th></tr>
    </thead>
    <tbody>
      <tr><td></td><td></td></tr>
      <tr><td></td><td></td></tr>
      <tr><td></td><td></td></tr>
      <tr><td></td><td></td></tr>
      <tr><td></td><td></td></tr>
    </tbody>
  </table>
</section>

</body>
</html>
```